Social Media App Needs PPT Template

We need a PowerPoint template for a new social media company based in the DC area called "Bold Ledger." We provide an interactive digital platform for executives to share actionable advice. We would like to see designs that use our orange logo color as an accent, but are mainly grey, white, and black. The final design should communicate clean, chic, modern, and professional.

Target Market(s)

Executives

Industry/Entity Type

Information Technology

Font styles to use
Sans Serif

Colors
f78f20
fbe7d2
ffffff
000000
e8e8e8
757575

Requirements
Must have
• My project must have title page and many options for the body of the ppt (graphs, tables, etc). It also needs to be easy to modify. I must have someone who is experienced in creating powerpoint templates.
Nice to have
• It would be nice to have a very modern and clean design that includes the logo on every page, but still leaves a lot of room for the content of the slide
Should not have
• My design project should not look to busy.

```html
<!DOCTYPE html>
<html lang="en">
<head>
<meta charset="utf-8">
<title>Bold Ledger – Stats Slide</title>
<link href="https://fonts.googleapis.com/css2?family=Lato:wght@300;400;700&family=Oswald:wght@500&display=swap" rel="stylesheet">
<style>
  :root {
    --stage: #555555;
    --paper: #ffffff;
    --accent: #f3951f;
    --navy: #222d3b;
    --slate: #6d6e70;
    --ink: #231f20;
    --muted: #7a7a7a;
    --rule: #6d6e70;
  }
  * { margin: 0; padding: 0; box-sizing: border-box; }
  html, body { width: 1200px; height: 960px; overflow: hidden; }
  body {
    background: var(--stage);
    font-family: "Lato", Arial, sans-serif;
    position: relative;
  }
  .page-label {
    position: absolute; top: 74px; left: 0; width: 1200px;
    text-align: center; color: #f2f2f2;
    font-weight: 300; font-size: 27px; letter-spacing: 0.5px;
  }
  .slide {
    position: absolute; left: 123px; top: 159px;
    width: 987px; height: 741px; background: var(--paper);
  }
  .accent-stripe {
    position: absolute; left: 0; top: 15px; width: 100%; height: 11px;
    background: var(--accent);
  }
  .header-band {
    position: absolute; left: 0; top: 29px; width: 100%; height: 95px;
    background: var(--navy);
  }
  .slide-title {
    position: absolute; left: 42px; top: 14px;
    font-family: "Oswald", "Arial Narrow", sans-serif; font-weight: 500;
    font-size: 47px; color: #fff; letter-spacing: -0.5px; line-height: 64px;
    transform: scaleX(0.92); transform-origin: left center;
  }
  .brand {
    position: absolute; right: 46px; top: 30px;
    display: flex; align-items: center; gap: 10px;
    color: #fff; font-weight: 700; font-size: 26px; line-height: 36px;
  }
  .brand-dot {
    width: 20px; height: 20px; border-radius: 50%; background: var(--accent);
  }
  .stat-card {
    position: absolute; width: 423px; height: 190px; color: #fff;
  }
  .stat-card.orange { left: 46px;  top: 173px; background: var(--accent); }
  .stat-card.slate  { left: 519px; top: 173px; background: var(--slate); }
  .stat-card.navy   { left: 46px;  top: 409px; background: var(--navy); }
  .stat-card.ink    { left: 519px; top: 409px; background: var(--ink); }
  .stat-icon {
    position: absolute; left: 24px; top: 50%; transform: translateY(-50%);
    width: 90px; height: 90px;
  }
  .stat-text { position: absolute; left: 141px; top: 26px; width: 260px; }
  .stat-value {
    font-weight: 400; font-size: 39px; line-height: 46px; letter-spacing: 0.3px;
    margin-bottom: 4px;
  }
  .stat-copy { font-size: 17px; line-height: 21.6px; font-weight: 400; }
  .footer-rule {
    position: absolute; left: 663px; top: 684px; width: 290px; height: 1px;
    background: var(--rule);
  }
  .footer-meta {
    position: absolute; right: 35px; top: 703px;
    font-size: 13.5px; color: var(--muted); font-weight: 400;
  }
  .footer-meta .sep { margin: 0 7px; }
</style>
</head>
<body>
  <div class="page-label">Page 11</div>

  <section class="slide">
    <div class="accent-stripe"></div>
    <header class="header-band">
      <h1 class="slide-title">TITLE GOES HERE</h1>
      <div class="brand"><span class="brand-dot"></span>Bold Ledger</div>
    </header>

    <article class="stat-card orange">
      <svg class="stat-icon" viewBox="0 0 90 90" fill="none" stroke="#fff" stroke-width="4" stroke-linejoin="round" aria-hidden="true">
        <rect x="4" y="36" width="10" height="22" rx="2"/>
        <path d="M14 38 L62 24 L62 70 L14 56 Z"/>
        <path d="M24 58 L26 70 L40 70 L38 61"/>
        <rect x="62" y="20" width="8" height="54" rx="2"/>
        <path d="M76 38 L86 34 M76 47 L88 47 M76 56 L86 60" stroke-linecap="round"/>
      </svg>
      <div class="stat-text">
        <p class="stat-value">915,456,459</p>
        <p class="stat-copy">Lorem ipsum dolor sit amet, consectetuer adipiscing elit, s ed diam nonu mmy nibh euis mod tincidunt</p>
      </div>
    </article>

    <article class="stat-card slate">
      <svg class="stat-icon" viewBox="0 0 90 90" fill="none" stroke="#fff" stroke-width="4" stroke-linejoin="round" aria-hidden="true">
        <path d="M34 8 H56 L52 22 H38 Z"/>
        <path d="M38 22 C20 34 8 52 10 68 C12 80 24 84 45 84 C66 84 78 80 80 68 C82 52 70 34 52 22"/>
        <text x="45" y="66" text-anchor="middle" font-family="Lato, sans-serif" font-weight="700" font-size="34" fill="#fff" stroke="none">$</text>
      </svg>
      <div class="stat-text">
        <p class="stat-value">111,458,564</p>
        <p class="stat-copy">Lorem ipsum dolor sit amet, consectetuer adipiscing elit, s ed diam nonu mmy nibh euis mod tincidunt</p>
      </div>
    </article>

    <article class="stat-card navy">
      <svg class="stat-icon" viewBox="0 0 90 90" aria-hidden="true">
        <ellipse cx="44" cy="58" rx="30" ry="20" fill="#fff"/>
        <circle cx="16" cy="58" r="9" fill="#fff"/>
        <rect x="24" y="70" width="10" height="14" rx="3" fill="#fff"/>
        <rect x="54" y="70" width="10" height="14" rx="3" fill="#fff"/>
        <path d="M26 42 L22 30 L36 38 Z" fill="#fff"/>
        <circle cx="70" cy="20" r="11" fill="none" stroke="#fff" stroke-width="3"/>
        <text x="70" y="26" text-anchor="middle" font-family="Lato, sans-serif" font-weight="700" font-size="16" fill="#fff">$</text>
      </svg>
      <div class="stat-text">
        <p class="stat-value">100%</p>
        <p class="stat-copy">Lorem ipsum dolor sit amet, consectetuer adipiscing elit, s ed diam nonu mmy nibh euis mod tincidunt</p>
      </div>
    </article>

    <article class="stat-card ink">
      <svg class="stat-icon" viewBox="0 0 90 90" fill="none" stroke="#fff" stroke-width="4" aria-hidden="true">
        <rect x="6" y="62" width="16" height="20"/>
        <rect x="22" y="46" width="16" height="36"/>
        <rect x="38" y="30" width="16" height="52"/>
        <rect x="54" y="12" width="16" height="70"/>
      </svg>
      <div class="stat-text">
        <p class="stat-value">100%</p>
        <p class="stat-copy">Lorem ipsum dolor sit amet, consectetuer adipiscing elit, s ed diam nonu mmy nibh euis mod tincidunt</p>
      </div>
    </article>

    <div class="footer-rule"></div>
    <p class="footer-meta">www.boldledger.com<span class="sep">|</span>Page 9</p>
  </section>
</body>
</html>
```